Locksmith Business Cards

My father-in-law is in need of new business cards for his locksmith business and I need to impress him. Kindly help me out!

You can see the previous business card attached. It is a family run business in North Wales.

No individual names on the cards.

Key Things to Feature:
- The words "Prompt", "Local", "Reliable" (as you can see under the logo on the website)
- 24h Emergency Service
- Covering All of North Wales, the Wirral and Chester
- The color blue
- A key or a lock would be interesting (similar to the ones that come up when you google locksmith business card)

Optional (only if design includes bullet points, like the example below):
https://imgvaultcdn.net/samples/208314/55172/55172_3904821_208314_image.jpg
- Residential / Commercial / Automotive
- Alarms & Cameras
- Key Cutting & Safes

https://www.brynhafod-locksmiths.co.uk/

Industry/Entity Type

Locksmith

Contact Information for Business Card

01632 960 418
07700 900 362
brynhafodlocksmiths@mailvane.com
Brynhafod Locksmiths, The Willow Barn, 7 Tannery Rd., Llandudno LL99 4QX
www.brynhafod-locksmiths.co.uk

Requirements
Must have
• - The words "Prompt", "Local", "Reliable" (as you can see under the logo on the website)
• - 24h Emergency Service
• - Covering All of North Wales, the Wirral and Chester
Nice to have
• - A key or a lock would be interesting (similar to the ones that come up when you google locksmith business card)

```html
<!DOCTYPE html>
<html lang="en">
<head>
<meta charset="utf-8">
<title>Brynhafod Locksmiths – Business Card</title>
<link rel="stylesheet" href="https://fonts.googleapis.com/css2?family=Oswald:wght@500&family=Saira+Semi+Condensed:wght@500&family=Saira+Condensed:wght@500&family=Roboto+Condensed:wght@400&family=Montserrat:wght@600&display=swap">
<style>
  :root {
    --page-bg: #d9d6d2;
    --card-bg: #f1f2f4;
    --card-edge: #c9ccd3;
    --navy: #2c3766;
    --text: #2a3358;
    --tab: #4a5a90;
    --icon: #1e80c6;
    --rule: #9aa1b4;
  }
  * { box-sizing: border-box; margin: 0; padding: 0; }
  html, body {
    width: 1200px; height: 1054px; overflow: hidden;
    background: var(--page-bg);
  }
  .card {
    position: absolute; left: 100px; top: 227px;
    width: 1000px; height: 600px;
    background: var(--card-bg);
    border: 1px solid var(--card-edge);
    box-shadow: 0 10px 30px rgba(0,0,0,.12);
    overflow: hidden;
  }
  .side-tab {
    position: absolute; top: 184px; width: 30px; height: 330px;
    background: var(--tab);
  }
  .side-tab--left { left: 0; border-radius: 0 30px 30px 0; }
  .side-tab--right { right: 0; border-radius: 30px 0 0 30px; }

  .brand {
    position: absolute; left: 177px; top: 64px;
    display: flex; align-items: center; gap: 30px;
  }
  .brand__mark {
    width: 72px; height: 72px; background: var(--navy); border-radius: 6px;
  }
  .brand__name {
    font-family: "Oswald", "Roboto Condensed", sans-serif; font-weight: 500;
    font-size: 54px; line-height: 1; letter-spacing: 0.3px; word-spacing: 6px;
    color: var(--navy); text-transform: uppercase;
  }

  .contacts, .services {
    list-style: none; position: absolute; top: 252px;
    font-family: "Saira Semi Condensed", "Saira Condensed", "Roboto Condensed", "Arial Narrow", sans-serif;
    font-weight: 500; font-size: 23px; line-height: 32px; color: var(--text);
    white-space: nowrap;
  }
  .contacts { right: 544px; left: 60px; text-align: right; }
  .contacts li { display: flex; justify-content: flex-end; align-items: center; gap: 22px; }
  .contacts .icon { width: 20px; height: 20px; flex: none; fill: var(--icon); }
  .contacts .icon-spacer { width: 20px; flex: none; }

  .divider {
    position: absolute; left: 489px; top: 229px; width: 1px; height: 235px;
    background: var(--rule);
  }

  .services { left: 522px; right: 60px; }
  .services li { display: flex; align-items: center; gap: 22px; }
  .services .bullet {
    width: 8px; height: 8px; border-radius: 50%; background: var(--icon); flex: none;
  }
  .services .bullet--none { background: none; }

  .tagline {
    position: absolute; left: 0; right: 0; top: 528px; text-align: center;
    font-family: "Montserrat", sans-serif; font-weight: 600;
    font-size: 21px; letter-spacing: 2px; color: var(--navy);
  }
  .tagline .sep { margin: 0 12px; }
</style>
</head>
<body>
<main class="card">
  <div class="side-tab side-tab--left"></div>
  <div class="side-tab side-tab--right"></div>

  <header class="brand">
    <span class="brand__mark"></span>
    <h1 class="brand__name">Brynhafod Locksmiths</h1>
  </header>

  <ul class="contacts">
    <li>01632 960 418
      <svg class="icon" viewBox="0 0 24 24"><path d="M3 8c0-3 3-5 9-5s9 2 9 5v2h-5V8c-1-.6-2.3-1-4-1s-3 .4-4 1v2H3zM6 12h12l2 8H4z"/></svg></li>
    <li>07700 900 362
      <svg class="icon" viewBox="0 0 24 24"><path d="M3 8c0-3 3-5 9-5s9 2 9 5v2h-5V8c-1-.6-2.3-1-4-1s-3 .4-4 1v2H3zM6 12h12l2 8H4z"/></svg></li>
    <li>brynhafodlocksmiths@mailvane.com
      <svg class="icon" viewBox="0 0 24 24"><path d="M2 5h20v14H2zM2 5l10 8 10-8" stroke="#f1f2f4" stroke-width="1.6"/></svg></li>
    <li>www.brynhafod-locksmiths.co.uk
      <svg class="icon" viewBox="0 0 24 24"><circle cx="12" cy="12" r="10"/><path d="M2 12h20M12 2c-4 5-4 15 0 20M12 2c4 5 4 15 0 20M4 7h16M4 17h16" stroke="#f1f2f4" stroke-width="1.3" fill="none"/></svg></li>
    <li>The Willow Barn, 7 Tannery Rd.,
      <svg class="icon" viewBox="0 0 24 24"><path d="M12 2a7 7 0 0 0-7 7c0 5 7 13 7 13s7-8 7-13a7 7 0 0 0-7-7zm0 10a3 3 0 1 1 0-6 3 3 0 0 1 0 6z"/></svg></li>
    <li>Llandudno LL99 4QX <span class="icon-spacer"></span></li>
  </ul>

  <div class="divider"></div>

  <ul class="services">
    <li><span class="bullet"></span>24h Emergency Service</li>
    <li><span class="bullet"></span>Covering All of North Wales,</li>
    <li><span class="bullet bullet--none"></span>the Wirral and Chester</li>
    <li><span class="bullet"></span>Residential / Commercial / Automotive</li>
    <li><span class="bullet"></span>Alarms &amp; Cameras</li>
    <li><span class="bullet"></span>Key Cutting &amp; Safes</li>
  </ul>

  <p class="tagline">PROMPT<span class="sep">|</span>LOCAL<span class="sep">|</span>RELIABLE</p>
</main>
</body>
</html>
```